Need Business Card ASAP

We need a business card design for a meeting coming up in a few days. The company name is Harlow Ridge Building and Construction and the logo is attached. Something clean, cool, and contemporary that we can get to a printer right away. Attached is the business card for Volmar Energy, an affiliated company, which we like. Instead of the hawk on the back, you could use the attached "D". We'll also be needing matching letterhead in the near future, so ideas for that are welcome.

```html
<!DOCTYPE html>
<html lang="en">
<head>
<meta charset="utf-8">
<title>Harlow Ridge Building and Construction – Business Card</title>
<link href="https://fonts.googleapis.com/css2?family=Saira+Condensed:wght@600&family=Saira:wght@400;600&display=swap" rel="stylesheet">
<style>
  :root {
    --backdrop: #e9e6df;
    --card-white: #ffffff;
    --gold-light: #e4dfc2;
    --gold: #c9c097;
    --gold-deep: #a89f72;
    --ink: #221c1a;
    --text: #3a3a3a;
    --muted: #6b6b6b;
  }
  * { box-sizing: border-box; margin: 0; padding: 0; }
  html, body { width: 1200px; height: 991px; overflow: hidden; }
  body {
    background: var(--backdrop);
    font-family: "Saira", sans-serif;
    color: var(--text);
    position: relative;
  }
  .card {
    position: absolute;
    top: 145px;
    width: 400px;
    height: 700px;
    background: var(--card-white);
    box-shadow: 0 10px 30px rgba(0,0,0,0.18);
    overflow: hidden;
  }
  .card--front { left: 160px; }
  .card--back { left: 640px; }
  .card__shapes { position: absolute; inset: 0; width: 100%; height: 100%; }

  .brand {
    position: absolute;
    left: 0; right: 0;
    display: flex;
    align-items: center;
    justify-content: center;
    gap: 12px;
  }
  .card--front .brand { top: 170px; }
  .card--back .brand { top: 200px; }
  .brand__mark {
    width: 26px; height: 26px;
    background: var(--gold-deep);
    flex: none;
  }
  .brand__name {
    font-family: "Saira", sans-serif;
    font-weight: 600;
    font-size: 17px;
    line-height: 1.2;
    color: var(--ink);
    width: 210px;
  }

  .person {
    position: absolute;
    left: 34px;
    top: 300px;
  }
  .person__name {
    font-family: "Saira Condensed", sans-serif;
    font-weight: 600;
    font-size: 38px;
    letter-spacing: 1px;
    color: var(--text);
    line-height: 1;
  }
  .person__role {
    font-family: "Saira", sans-serif;
    font-size: 15px;
    letter-spacing: 2px;
    color: var(--muted);
    margin-top: 4px;
  }

  .contacts {
    position: absolute;
    left: 30px;
    top: 400px;
    display: grid;
    grid-template-columns: 150px 210px;
    row-gap: 16px;
    column-gap: 8px;
    font-size: 12.5px;
    color: var(--text);
  }
  .contact { display: flex; align-items: center; gap: 8px; white-space: nowrap; }
  .contact--wide { grid-column: 1 / span 2; }
  .contact__icon { width: 20px; height: 20px; flex: none; }
</style>
</head>
<body>

  <section class="card card--front" aria-label="Card front">
    <svg class="card__shapes" viewBox="0 0 400 700" preserveAspectRatio="none" aria-hidden="true">
      <defs>
        <linearGradient id="goldSweepFront" x1="0" y1="0" x2="1" y2="1">
          <stop offset="0" stop-color="#e4dfc2"/>
          <stop offset="1" stop-color="#c9c097"/>
        </linearGradient>
      </defs>
      <path d="M0,470 C150,600 290,650 400,650 L400,700 L0,700 Z" fill="url(#goldSweepFront)"/>
      <path d="M0,600 C80,660 160,690 230,700 L0,700 Z" fill="#221c1a"/>
    </svg>
    <div class="brand">
      <span class="brand__mark"></span>
      <span class="brand__name">Harlow Ridge Building and Construction</span>
    </div>
  </section>

  <section class="card card--back" aria-label="Card back">
    <svg class="card__shapes" viewBox="0 0 400 700" preserveAspectRatio="none" aria-hidden="true">
      <defs>
        <linearGradient id="goldSweepBack" x1="0" y1="0" x2="1" y2="1">
          <stop offset="0" stop-color="#e4dfc2"/>
          <stop offset="1" stop-color="#c9c097"/>
        </linearGradient>
      </defs>
      <path d="M110,0 C260,60 360,200 400,340 L400,0 Z" fill="url(#goldSweepBack)"/>
      <path d="M300,0 C345,35 380,80 400,125 L400,0 Z" fill="#221c1a"/>
    </svg>

    <div class="brand">
      <span class="brand__mark"></span>
      <span class="brand__name">Harlow Ridge Building and Construction</span>
    </div>

    <div class="person">
      <p class="person__name">ALDEN MARSH</p>
      <p class="person__role">GENERAL MANAGER</p>
    </div>

    <div class="contacts">
      <div class="contact">
        <svg class="contact__icon" viewBox="0 0 20 20" aria-hidden="true"><circle cx="10" cy="10" r="9" fill="none" stroke="#3a3a3a" stroke-width="1.3"/><path d="M7,5 L9,7 L8,9 Q9,11 11,12 L13,11 L15,13 L13.5,15 Q9,15 5,9 Z" fill="#3a3a3a"/></svg>
        <span>014 552 3190</span>
      </div>
      <div class="contact">
        <svg class="contact__icon" viewBox="0 0 20 20" aria-hidden="true"><circle cx="10" cy="10" r="9" fill="none" stroke="#3a3a3a" stroke-width="1.3"/><rect x="5.5" y="6.5" width="9" height="7" fill="none" stroke="#3a3a3a" stroke-width="1.3"/><path d="M5.5,6.5 L10,10.5 L14.5,6.5" fill="none" stroke="#3a3a3a" stroke-width="1.3"/></svg>
        <span>a.marsh@harlowridge.com</span>
      </div>
      <div class="contact">
        <svg class="contact__icon" viewBox="0 0 20 20" aria-hidden="true"><circle cx="10" cy="10" r="9" fill="none" stroke="#3a3a3a" stroke-width="1.3"/><rect x="7" y="4.5" width="6" height="11" rx="1" fill="none" stroke="#3a3a3a" stroke-width="1.3"/><circle cx="10" cy="13.5" r="0.8" fill="#3a3a3a"/></svg>
        <span>014 552 3191</span>
      </div>
      <div class="contact">
        <svg class="contact__icon" viewBox="0 0 20 20" aria-hidden="true"><circle cx="10" cy="10" r="9" fill="none" stroke="#3a3a3a" stroke-width="1.3"/><circle cx="10" cy="10" r="5" fill="none" stroke="#3a3a3a" stroke-width="1.1"/><path d="M5,10 H15 M10,5 Q7,10 10,15 M10,5 Q13,10 10,15" fill="none" stroke="#3a3a3a" stroke-width="1"/></svg>
        <span>www.harlowridge.com</span>
      </div>
      <div class="contact contact--wide">
        <svg class="contact__icon" viewBox="0 0 20 20" aria-hidden="true"><circle cx="10" cy="10" r="9" fill="none" stroke="#3a3a3a" stroke-width="1.3"/><path d="M10,15.5 C7,11.5 6.5,10 6.5,8.5 A3.5,3.5 0 0 1 13.5,8.5 C13.5,10 13,11.5 10,15.5 Z" fill="#3a3a3a"/><circle cx="10" cy="8.5" r="1.3" fill="#ffffff"/></svg>
        <span>42 Ridgeway Road, Suite 7, Eastwood Park</span>
      </div>
    </div>
  </section>

</body>
</html>
```